Footwear Retail Chain Store Needs New Design for Display Clip

We have several retail shoe stores in Canada. As part of our display of boots, we identify our boots that are waterproof, so that customers can easily obtain information.

What we require:

- We need a design to be printed on a plastic clip of the exact dimensions as in the attachment with the intent of advising consumers which boots are WATERPROOF;
- The utility of the clip is to place it on boots that are displayed to the consumers in the stores;
- We want a design where we are advising consumers that the boot is WATERPROOF – we want a design that is different from the attached pictures (as there may be copyright issues with the image);
- The word “WATERPROOF” should be visible clearly on the clip;
- Despite the word being there, the design on its own should reflect the concept of waterproof without even having to read the word.

Then, we want the exact same design, except that the word "waterproof" should be changed to "Water Resistant".

Target Market(s)

The clip will be placed on all various sorts of boots, for all types and age group of customers.

Industry/Entity Type

Store

Requirements
Must have
• - A very nice image in the background of the clip that symbolizes waterproof;
• - the words "waterproof" or "water resistant" on the front

```html
<!DOCTYPE html>
<html lang="en">
<head>
<meta charset="utf-8">
<title>Waterproof and Water Resistant Display Clip</title>
<link rel="stylesheet" href="https://fonts.googleapis.com/css2?family=Russo+One&display=swap">
<style>
  :root {
    --frame-navy: #0c0b45;
    --stage-grey: #d9d6d2;
    --water-pale: #cfefff;
    --water-light: #8cc8f2;
    --water-mid: #3f86e6;
    --water-deep: #1a4fcf;
    --label-white: #ffffff;
    --label-shadow: #0d0a5c;
  }
  * { margin: 0; padding: 0; box-sizing: border-box; }
  html, body {
    width: 1200px;
    height: 831px;
    overflow: hidden;
    background: var(--frame-navy);
  }
  .sheet {
    position: relative;
    width: 1200px;
    height: 831px;
    background: var(--frame-navy);
  }
  .stage {
    position: absolute;
    left: 35px;
    top: 22px;
    width: 710px;
    height: 786px;
    background: var(--stage-grey);
  }
  .clip {
    position: absolute;
    overflow: hidden;
    font-family: "Russo One", sans-serif;
    color: var(--label-white);
    text-align: center;
  }
  .clip--hero { left: 70px; top: 68px; width: 655px; height: 650px; border-radius: 10px; }
  .clip--waterproof { left: 790px; top: 25px; width: 375px; height: 363px; }
  .clip--resistant { left: 790px; top: 432px; width: 375px; height: 373px; }
  .clip__backdrop {
    position: absolute;
    inset: 0;
    width: 100%;
    height: 100%;
  }
  .clip__word {
    position: absolute;
    left: 0;
    right: 0;
    line-height: 1;
    letter-spacing: 0.01em;
    text-shadow: 6px 6px 0 var(--label-shadow);
  }
  .clip--hero .clip__word--main { top: 248px; font-size: 138px; transform: scaleY(1.05); }
  .clip--hero .clip__word--sub { top: 428px; font-size: 82px; text-shadow: 5px 5px 0 var(--label-shadow); }
  .clip--waterproof .clip__word--single { top: 146px; font-size: 45px; text-shadow: 3px 3px 0 var(--label-shadow); }
  .clip--resistant .clip__word--main { top: 112px; font-size: 80px; text-shadow: 4px 4px 0 var(--label-shadow); }
  .clip--resistant .clip__word--sub { top: 208px; font-size: 48px; text-shadow: 3px 3px 0 var(--label-shadow); }
</style>
</head>
<body>
<main class="sheet">
  <div class="stage"></div>

  <section class="clip clip--hero">
    <svg class="clip__backdrop" viewBox="0 0 100 100" preserveAspectRatio="none" role="img" aria-label="Photograph of water droplets on a blue surface framed by a splashing wave of water">
      <defs>
        <radialGradient id="waterHero" cx="55%" cy="55%" r="75%">
          <stop offset="0" stop-color="var(--water-deep)"/>
          <stop offset="0.45" stop-color="var(--water-mid)"/>
          <stop offset="0.8" stop-color="var(--water-light)"/>
          <stop offset="1" stop-color="var(--water-pale)"/>
        </radialGradient>
      </defs>
      <rect width="100" height="100" fill="url(#waterHero)"/>
    </svg>
    <div class="clip__word clip__word--main">WATER</div>
    <div class="clip__word clip__word--sub">RESISTANT</div>
  </section>

  <section class="clip clip--waterproof">
    <svg class="clip__backdrop" viewBox="0 0 100 100" preserveAspectRatio="none" role="img" aria-label="Photograph of water droplets on a blue surface framed by a splashing wave of water">
      <defs>
        <radialGradient id="waterProof" cx="55%" cy="60%" r="75%">
          <stop offset="0" stop-color="var(--water-deep)"/>
          <stop offset="0.45" stop-color="var(--water-mid)"/>
          <stop offset="0.8" stop-color="var(--water-light)"/>
          <stop offset="1" stop-color="var(--water-pale)"/>
        </radialGradient>
      </defs>
      <rect width="100" height="100" fill="url(#waterProof)"/>
    </svg>
    <div class="clip__word clip__word--single">WATERPROOF</div>
  </section>

  <section class="clip clip--resistant">
    <svg class="clip__backdrop" viewBox="0 0 100 100" preserveAspectRatio="none" role="img" aria-label="Photograph of water droplets on a blue surface framed by a splashing wave of water">
      <defs>
        <radialGradient id="waterResist" cx="55%" cy="55%" r="75%">
          <stop offset="0" stop-color="var(--water-deep)"/>
          <stop offset="0.45" stop-color="var(--water-mid)"/>
          <stop offset="0.8" stop-color="var(--water-light)"/>
          <stop offset="1" stop-color="var(--water-pale)"/>
        </radialGradient>
      </defs>
      <rect width="100" height="100" fill="url(#waterResist)"/>
    </svg>
    <div class="clip__word clip__word--main">WATER</div>
    <div class="clip__word clip__word--sub">RESISTANT</div>
  </section>
</main>
</body>
</html>
```